Initial website for sport tech startup

We are currently in the R&D phases of our new product. It’s a headband to prevent concussion in the soccer market initially.

We have 2 products, one that’s basic aimed at the youth market and the other more technology driven that’s aimed at the academies and professional market.

Initially the product will launch in the UK

Target Market(s)

Youth soccer players and parents in UK, Soccer Clubs, Federations.

Industry/Entity Type

Sporting Good

Coding

Coded - Design and coding required

Number of Pages Required

5+ page

Requirements
Must have
• Professional style that can be adapted and changed over the coming months.
Nice to have
• Ecommerce ability in the future.

```html
<!DOCTYPE html>
<html lang="en">
<head>
<meta charset="utf-8">
<title>Helmara – Head Protection for Sport</title>
<link rel="stylesheet" href="https://fonts.googleapis.com/css2?family=Montserrat:wght@500;600;700;800&family=Roboto:ital,wght@0,400;0,500;1,400&display=swap">
<style>
:root{
  --blue:#0d4a8a;
  --blue-dark:#093a6e;
  --ink:#1b1b1b;
  --text:#3d3d3d;
  --muted:#6b6b6b;
  --night:#151515;
  --white:#ffffff;
  --line:#dcdcdc;
}
*{margin:0;padding:0;box-sizing:border-box}
html,body{width:1200px;height:4054px;overflow:hidden;background:var(--white)}
body{position:relative;font-family:'Roboto',Arial,sans-serif;color:var(--text)}
.abs{position:absolute}
.heading{font-family:'Montserrat',sans-serif;font-weight:700;color:var(--ink);text-transform:uppercase;letter-spacing:.5px}
.heading span{color:var(--blue)}
.body-copy{font-size:13.6px;line-height:24.8px;color:var(--text)}

/* hero */
.hero{left:0;top:0;width:1200px;height:635px;background:radial-gradient(ellipse at 65% 55%,#4a4a48 0%,#2a2a2a 45%,#141414 100%)}
.hero-turf{left:0;top:470px;width:1200px;height:165px;background:linear-gradient(180deg,rgba(30,45,25,0),#1d2a17 70%,#17210f)}
.brand{font-family:'Montserrat',sans-serif;font-weight:600;letter-spacing:2px;display:flex;align-items:center;gap:10px}
.brand i{display:block;width:12px;height:12px;background:var(--blue)}
.header-brand{left:151px;top:38px;height:42px;font-size:28px;color:#c9d3de}
.nav{left:381px;top:53px;font-family:'Montserrat',sans-serif;font-weight:700;font-size:14.5px;color:var(--white)}
.nav a{position:absolute;top:0;white-space:nowrap;color:inherit;text-decoration:none}
.nav .active::after{content:"";position:absolute;left:0;top:22px;width:34px;height:3px;background:var(--blue)}
.welcome-frame{left:206px;top:252px;width:786px;height:178px;border:8px solid var(--blue)}
.welcome{left:206px;top:300px;width:786px;text-align:center;font-family:'Montserrat',sans-serif;font-weight:700;font-size:53px;color:var(--white);letter-spacing:.5px}
.arrow{top:305px}

/* partners */
.partners{left:0;top:635px;width:1200px;height:115px;border-bottom:1px solid var(--line);display:flex;justify-content:center;align-items:center;gap:70px}
.partner{background:#c8ccd3}
.rule{left:0;width:1200px;height:1px;background:var(--line)}

/* mission */
.mission-title{left:173px;top:806px;font-size:43px}
.mission-copy{left:173px;top:867px;width:425px}
.mission-frame{left:649px;top:847px;width:394px;height:226px;border:4px solid var(--blue)}
.mission-photo{left:614px;top:808px;width:414px;height:249px;background:linear-gradient(135deg,#2b3e5a,#6a7a8a 45%,#3b4a2c 80%,#2a2a24)}

/* cards */
.section-title{left:0;width:1200px;text-align:center;font-size:43px}
.card-frame{left:128px;width:945px;border:4px solid var(--blue)}
.card{width:262px;background:var(--white);box-shadow:0 2px 14px rgba(0,0,0,.12)}
.card-photo{height:172px}
.card h3{font-family:'Montserrat',sans-serif;font-weight:700;font-size:17px;color:var(--ink);margin:33px 20px 10px}
.card p{font-size:12.4px;line-height:20.5px;color:var(--muted);margin:0 20px}
.read-more{display:inline-flex;align-items:center;gap:6px;font-family:'Montserrat',sans-serif;font-weight:700;font-size:12.6px;color:var(--blue);margin:14px 20px 0}
.pill{left:512px;width:176px;height:45px;border-radius:23px;background:var(--blue);color:var(--white);font-family:'Montserrat',sans-serif;font-weight:700;font-size:14px;display:flex;align-items:center;justify-content:center}

/* market band */
.band{left:0;top:1857px;width:1200px;height:384px;background:var(--blue)}
.band-left{left:0;top:1885px;width:655px;height:328px;background:linear-gradient(90deg,#232323,#333 80%,#2a2a2a)}
.band-right{left:810px;top:1885px;width:390px;height:328px;background:linear-gradient(90deg,#262626,#1a1a1a)}
.band-mid{left:655px;top:1857px;width:155px;height:384px;background:#161616}
.band-copy h2{font-family:'Montserrat',sans-serif;font-weight:700;font-size:36px;color:var(--white);letter-spacing:.5px}
.band-copy p{font-size:13.6px;line-height:24.8px;color:#ececec;margin-top:10px}

/* product */
.product-title{left:172px;top:2318px;font-size:43px}
.product-copy{left:172px;top:2381px;width:420px}
.product-art{left:650px;top:2328px;width:441px;height:286px;background:radial-gradient(ellipse at 55% 45%,#4a5060 0%,#3a3f4c 40%,#f3f3f3 72%)}

/* people */
.person{text-align:center}
.avatar{width:115px;height:115px;border-radius:50%;margin:22px auto 20px;background:linear-gradient(160deg,#c9b6a8,#8d7b70)}
.person h3{font-family:'Montserrat',sans-serif;font-weight:700;font-size:14px;color:var(--ink);margin:0}
.person .role{font-family:'Montserrat',sans-serif;font-weight:700;font-size:12.6px;color:var(--blue);margin-top:10px}
.person p{font-size:12.4px;line-height:21.5px;color:var(--muted);margin:12px 30px 0}
.person .read-more{margin-top:16px}

/* testimonial + footer */
.dark{left:0;top:3484px;width:1200px;height:570px;background:linear-gradient(180deg,#121212,#1d1d1d 60%,#151515)}
.quote-box{left:128px;top:3404px;width:945px;height:226px;border:4px solid var(--blue);background:var(--white)}
.quote-gap{left:286px;top:3400px;width:618px;height:10px;background:var(--white)}
.quote-mark{font-family:'Montserrat',sans-serif;font-weight:800;font-size:86px;color:var(--blue);line-height:1}
.quote-head{left:0;top:3388px;width:1200px;text-align:center;font-family:'Montserrat',sans-serif;font-weight:600;font-size:17.5px;line-height:27px;color:var(--blue)}
.quote-head b{color:#333;font-weight:600}
.quote-text{left:380px;top:3452px;width:440px;text-align:center;font-style:italic;font-size:13.6px;line-height:24.8px;color:#444}
.dots{left:0;top:3580px;width:1200px;display:flex;justify-content:center;gap:4px}
.dots i{width:10px;height:10px;border-radius:50%;background:#111}
.dots i.on{background:var(--blue)}
.footer-brand{left:472px;top:3668px;width:256px;height:62px;border:3px solid var(--white);justify-content:center;font-size:36px;color:var(--white)}
.fcol h4{font-family:'Montserrat',sans-serif;font-weight:700;font-size:17px;color:var(--white);margin-bottom:18px}
.fcol li{list-style:none;font-size:11px;line-height:22px;color:#cfcfcf}
.contact-row{display:flex;gap:9px;font-size:11px;line-height:17px;color:#cfcfcf;margin-bottom:14px}
.footer-rule{left:173px;top:3982px;width:854px;height:1px;background:#3a3a3a}
.copyright{left:173px;top:4009px;font-size:11px;color:var(--white)}
.social{top:4005px;width:22px;height:22px;border-radius:50%;background:var(--blue)}
</style>
</head>
<body>

<!-- hero -->
<div class="abs hero" role="img" aria-label="Close-up of a footballer's boot on the ball on a floodlit pitch"></div>
<div class="abs hero-turf"></div>
<div class="abs brand header-brand"><i></i>HELMARA</div>
<nav class="abs nav">
  <a class="active" style="left:0">HOME</a>
  <a style="left:99px">ABOUT</a>
  <a style="left:206px">MARKET</a>
  <a style="left:318px">SOCCER PLAYERS</a>
  <a style="left:504px">TEAM</a>
  <a style="left:595px">CONTACT</a>
</nav>
<div class="abs welcome-frame"></div>
<h1 class="abs welcome">WELCOME TO HELMARA</h1>
<svg class="abs arrow" style="left:58px" width="32" height="72" viewBox="0 0 32 72"><path d="M30 2 L2 36 L30 70" fill="none" stroke="#cfcfcf" stroke-width="2"/></svg>
<svg class="abs arrow" style="left:1122px" width="32" height="72" viewBox="0 0 32 72"><path d="M2 2 L30 36 L2 70" fill="none" stroke="#cfcfcf" stroke-width="2"/></svg>

<!-- partners -->
<div class="abs partners">
  <div class="partner" style="width:132px;height:30px"></div>
  <div class="partner" style="width:130px;height:52px;border-radius:4px"></div>
  <div class="partner" style="width:40px;height:52px;border-radius:50%"></div>
  <div class="partner" style="width:115px;height:48px"></div>
  <div class="partner" style="width:40px;height:54px"></div>
  <div class="partner" style="width:100px;height:42px"></div>
</div>

<!-- mission -->
<h2 class="abs heading mission-title">Our <span>Mission</span></h2>
<p class="abs body-copy mission-copy">Helmara is designing and developing head protection products to reduce the likelihood of concussion when playing sports. Exploring and understanding medical insights, material science and composites research, current and former players experiences and governing bodies guidelines has allowed Helmara to develop the safety, style, form and function requirements of a suitable product to bring to market in Q4 2020.</p>
<div class="abs mission-frame"></div>
<div class="abs mission-photo" role="img" aria-label="Players gathered around an injured teammate lying on the pitch"></div>
<div class="abs rule" style="top:1147px"></div>

<!-- about -->
<h2 class="abs heading section-title" style="top:1203px">About <span>Helmara</span></h2>
<div class="abs card-frame" style="top:1383px;height:370px"></div>
<article class="abs card" style="left:173px;top:1306px;height:353px">
  <div class="card-photo" role="img" aria-label="Football boot striking a ball on wet grass" style="background:linear-gradient(135deg,#1c1c1c,#5a5a52 55%,#2c3320)"></div>
  <h3>HELMARA APPROACH</h3>
  <p>Using the most advanced composite materials to provide protection and an opportunity for data collection</p>
  <div class="read-more">READ MORE <svg width="18" height="8" viewBox="0 0 18 8"><path d="M0 4H16M12 1l4 3-4 3" fill="none" stroke="currentColor" stroke-width="1.6"/></svg></div>
</article>
<article class="abs card" style="left:469px;top:1306px;height:353px">
  <div class="card-photo" role="img" aria-label="Hands above a glowing growth chart" style="background:linear-gradient(135deg,#0f0f12,#3b2a22 50%,#16171c)"></div>
  <h3>MARKETING STRATEGY</h3>
  <p>Engage at all levels, youth, academies, professionals and amateurs With our initial product we will directly</p>
  <div class="read-more">READ MORE <svg width="18" height="8" viewBox="0 0 18 8"><path d="M0 4H16M12 1l4 3-4 3" fill="none" stroke="currentColor" stroke-width="1.6"/></svg></div>
</article>
<article class="abs card" style="left:765px;top:1306px;height:353px">
  <div class="card-photo" role="img" aria-label="Player in red kicking a ball in a stadium" style="background:linear-gradient(180deg,#5b6f83,#8c9aa4 45%,#3f7a36)"></div>
  <h3>FINANCIAL MODEL</h3>
  <p>Using the most advanced composite materials to provide protection and an opportunity for data collection</p>
  <div class="read-more">READ MORE <svg width="18" height="8" viewBox="0 0 18 8"><path d="M0 4H16M12 1l4 3-4 3" fill="none" stroke="currentColor" stroke-width="1.6"/></svg></div>
</article>
<div class="abs pill" style="top:1725px">READ MORE ABOUT</div>

<!-- market band -->
<div class="abs band"></div>
<div class="abs band-left" role="img" aria-label="Dark stadium background"></div>
<div class="abs band-mid"></div>
<div class="abs band-right" role="img" aria-label="Dark stadium background"></div>
<div class="abs band-copy" style="left:112px;top:1950px;width:385px">
  <h2>THE MARKET</h2>
  <p>Soccer has no head protection product despite recent high profile head injuries, concern over the long term damage of heading the ball and greater damage of concussion in women. There are in excess of 11m people actively playing football in the UK alone (8m men, 3m women).</p>
</div>
<div class="abs band-copy" style="left:864px;top:1950px;width:300px">
  <h2>TECHNOLOGY</h2>
  <p>A day doesn’t go by without a report of a game being held up for a concussion injury or a player being stretchered off up and down the country on a weekend, from youth football to men’s and women’s Sunday league.</p>
</div>

<!-- product -->
<h2 class="abs heading product-title">The <span>Product</span></h2>
<p class="abs body-copy product-copy">Our initial product will be simplistic in function and design to ensure we get to market in 2020. Further versions of the product will incorporate data tracking technologies to enhance analytical streams available to players and clubs. Starting with soccer, followed by other markets such as netball and field hockey, where the same issues exist today. We will create a new sector of sports apparel that will serve all communities of sport and allow for new categories of sponsorship and branding.</p>
<div class="abs product-art" role="img" aria-label="Product rendering of the protective headband"></div>

<!-- people -->
<h2 class="abs heading section-title" style="top:2668px">Our <span>People</span></h2>
<div class="abs card-frame" style="top:2848px;height:368px"></div>
<article class="abs card person" style="left:173px;top:2769px;height:353px">
  <div class="avatar" role="img" aria-label="Portrait photo of the founder"></div>
  <h3>MARTIN ASHDOWN</h3>
  <div class="role">FOUNDER / CEO</div>
  <p>Martin has a wealth of experience of growing start-ups and exiting businesses, from professional services to technology.</p>
  <div class="read-more">READ MORE <svg width="18" height="8" viewBox="0 0 18 8"><path d="M0 4H16M12 1l4 3-4 3" fill="none" stroke="currentColor" stroke-width="1.6"/></svg></div>
</article>
<article class="abs card person" style="left:469px;top:2769px;height:353px">
  <div class="avatar" role="img" aria-label="Portrait photo of the co-founder" style="background:linear-gradient(160deg,#8fa0b3,#57677a)"></div>
  <h3>HELEN CARROW</h3>
  <div class="role">CO –FOUNDER / COO</div>
  <p>Helen has a wealth of experience of growing start-ups and exiting businesses, from professional services to technology.</p>
  <div class="read-more">READ MORE <svg width="18" height="8" viewBox="0 0 18 8"><path d="M0 4H16M12 1l4 3-4 3" fill="none" stroke="currentColor" stroke-width="1.6"/></svg></div>
</article>
<article class="abs card person" style="left:765px;top:2769px;height:353px">
  <div class="avatar" role="img" aria-label="Portrait photo of the chief commercial officer" style="background:linear-gradient(160deg,#b9c1c9,#6f6a65)"></div>
  <h3>GRAHAM TOLLEY</h3>
  <div class="role">CCO</div>
  <p>Graham started his career in retail banking, later experience in corporate and private banking. Since leaving the corporate world in 2007.</p>
  <div class="read-more">READ MORE <svg width="18" height="8" viewBox="0 0 18 8"><path d="M0 4H16M12 1l4 3-4 3" fill="none" stroke="currentColor" stroke-width="1.6"/></svg></div>
</article>
<div class="abs pill" style="top:3188px">MEET OUR TEAM</div>

<!-- testimonial -->
<div class="abs dark" role="img" aria-label="Dark background of a player's boots on the pitch"></div>
<div class="abs quote-box"></div>
<div class="abs quote-gap"></div>
<div class="abs quote-mark" style="left:342px;top:3366px">“</div>
<div class="abs quote-mark" style="left:796px;top:3366px">”</div>
<div class="abs quote-head">CHIEF EXECUTIVE, COUNTY<br><b>LEAGUE, NORTH REGION</b></div>
<p class="abs quote-text">We are seeing more and more children come to matches with home-made head protection. In addition, we are having more concern from parents about heading the ball and getting asked more about our guidelines on heading and head injuries</p>
<div class="abs dots"><i></i><i class="on"></i><i></i><i></i><i></i></div>

<!-- footer -->
<div class="abs brand footer-brand">HELMARA</div>
<div class="abs fcol" style="left:173px;top:3774px;width:240px">
  <h4>Contact</h4>
  <div class="contact-row"><svg width="18" height="20" viewBox="0 0 18 20"><path d="M9 19s7-7 7-11a7 7 0 0 0-14 0c0 4 7 11 7 11z" fill="none" stroke="#ccc" stroke-width="1.3"/><circle cx="9" cy="8" r="2.5" fill="none" stroke="#ccc" stroke-width="1.3"/></svg><span>12 Harbour Lane,<br>Kestwick, KW4 7PL</span></div>
  <div class="contact-row"><svg width="20" height="18" viewBox="0 0 20 18"><path d="M4 1l4 4-2 3c1 2 3 4 5 5l3-2 4 4-3 2C9 16 2 9 1 4z" fill="none" stroke="#ccc" stroke-width="1.3"/></svg><span>Telephone: +44 20 0000 1234</span></div>
  <div class="contact-row"><svg width="22" height="16" viewBox="0 0 22 16"><rect x="1" y="1" width="20" height="14" fill="none" stroke="#ccc" stroke-width="1.3"/><path d="M1 1l10 8 10-8" fill="none" stroke="#ccc" stroke-width="1.3"/></svg><span>Email Us: hello@helmara.example</span></div>
</div>
<div class="abs fcol" style="left:455px;top:3774px"><h4>What We Do</h4><ul><li>Lorem ipsum dolo</li><li>Consectetur adipiscing elit.</li><li>Fusce eget leo tincid</li><li>Donec consequat</li><li>Praesent elementum</li><li>Aenean a ex eu lectu</li></ul></div>
<div class="abs fcol" style="left:687px;top:3774px"><h4>Company</h4><ul><li>Lorem ipsum dolo</li><li>Consectetur adipiscing elit.</li><li>Fusce eget leo tincid</li><li>Donec consequat</li><li>Praesent elementum</li><li>Aenean a ex eu lectu</li></ul></div>
<div class="abs fcol" style="left:887px;top:3774px"><h4>Other Links</h4><ul><li>Lorem ipsum dolo</li><li>Consectetur adipiscing elit.</li><li>Fusce eget leo tincid</li><li>Donec consequat</li><li>Praesent elementum</li><li>Aenean a ex eu lectu</li></ul></div>
<div class="abs footer-rule"></div>
<p class="abs copyright">Copyright 2020 All Rights Reserved</p>
<div class="abs social" style="left:944px"></div>
<div class="abs social" style="left:975px"></div>
<div class="abs social" style="left:1006px"></div>

</body>
</html>
```